Varnik Holdings — Business Card Design Brief
Overview
Design a double-sided business card for Varnik Holdings that highlights our two service arms: Varnik Communications (telecommunications) and Varnik Energy (business energy solutions). The card should feel smart and stand out when handed to clients.

Objectives
Showcase our areas of specialty clearly.
Reflect the overall Varnik / Varnik Holdings brand while acknowledging both arms.
Explore using both logos (Communications + Energy) or one unified logo, depending on the design.

Deliverables
One double-sided business card design (front + back).

Content & Copy
Front (preferred): Logo: Varnik / Varnik Holdings
Descriptor: Business Communications | Business Energy
Back:My contact details and company details
Core products: Business Mobile • Telephony • Internet • Business Energy Solutions

Brand & Visual Direction
We have a group logo currently tailored more toward telecoms, plus a separate Varnik Energy logo.
Please explore layouts that use both logos or just one, whichever works best.
Color: I wouldn't mind seeing an option using our the Blue/Purple gradient from our website (varnik-example.co.uk), but also open to non-gradient approaches and other colours..

Overall look: Smart, modern, and distinctive.
Format & Print Specs
Double-sided business card format. (Use a standard size

Must-Haves
Front: Varnik wording or Varnik Holdings wording with atleast 1 logo also on front “Business Communications | Business Energy.”

Back: Contact + company details and core products.
A design that stands out while remaining professional.

Nice-to-Have Options
A gradient version using our site’s Blue/Purple gradient.
A non-gradient version.
A dual-logo treatment versus a single-logo treatment.

Thanks
Owen

```html
<!DOCTYPE html>
<html lang="en">
<head>
<meta charset="utf-8">
<title>Varnik Holdings – Business Card</title>
<link rel="stylesheet" href="https://fonts.googleapis.com/css2?family=Montserrat:wght@400;600;700;800&family=Poppins:wght@600;700&family=Tinos&display=swap">
<style>
  :root {
    --stage: #9a9a9a;
    --card: #ffffff;
    --navy: #1c1466;
    --green: #45ac0e;
    --blue: #1a63d8;
    --ink: #1f1f1f;
    --charcoal: #333333;
    --rule: #8a8a8a;
  }
  * { margin: 0; padding: 0; box-sizing: border-box; }
  html, body { width: 1200px; height: 1059px; overflow: hidden; }
  body { background: var(--stage); position: relative; font-family: "Montserrat", sans-serif; }

  .card {
    position: absolute;
    background: var(--card);
    border-radius: 24px;
    overflow: hidden;
    box-shadow: 0 14px 22px rgba(0,0,0,0.35);
  }
  .card--front { left: 252px; top: 88px; width: 724px; height: 415px; }
  .card--back  { left: 252px; top: 567px; width: 712px; height: 406px; }

  /* front: brand block */
  .brand-block {
    position: absolute; left: 72px; top: 90px; width: 266px;
    display: flex; flex-direction: column; align-items: center;
  }
  .brand-mark { width: 96px; height: 96px; border-radius: 50%; background: var(--green); }
  .brand-name {
    margin-top: 14px;
    font-family: "Montserrat", sans-serif; font-weight: 800;
    font-size: 50px; letter-spacing: 1px; color: var(--navy); line-height: 1;
  }
  .brand-descriptor {
    margin-top: 9px;
    font-weight: 600; font-size: 10.5px; color: var(--navy);
    white-space: nowrap; line-height: 1.2;
  }
  .divider { position: absolute; left: 357px; top: 71px; width: 1px; height: 223px; background: var(--rule); }

  .contact { position: absolute; left: 386px; top: 62px; }
  .contact__name { font-weight: 700; font-size: 28px; color: var(--navy); line-height: 1.2; }
  .contact__role { font-family: "Tinos", serif; font-size: 17px; color: var(--ink); margin-top: 4px; }
  .contact__list { list-style: none; margin-top: 12px; }
  .contact__item {
    display: flex; align-items: center; gap: 11px;
    font-size: 19px; color: var(--ink); height: 33.5px;
  }
  .contact__item svg { width: 18px; height: 18px; flex: none; }

  .services {
    position: absolute; left: 0; right: 0; top: 321px; text-align: center;
    font-weight: 700; font-size: 19px; color: var(--navy); line-height: 28px;
  }

  .band { position: absolute; left: 0; right: 0; bottom: 0; height: 12px; }

  /* back */
  .group-title {
    position: absolute; left: 0; right: 0; top: 66px; text-align: center;
    font-family: "Poppins", sans-serif; font-weight: 700; font-size: 54px; color: var(--charcoal);
  }
  .back-brand {
    position: absolute; left: 0; right: 0; top: 160px;
    display: flex; flex-direction: column; align-items: center;
  }
  .back-brand .brand-mark { background: var(--blue); width: 110px; height: 110px; }
  .back-brand .brand-name { font-size: 56px; margin-top: 18px; }
</style>
</head>
<body>

<section class="card card--front" aria-label="Card front">
  <div class="brand-block">
    <div class="brand-mark" aria-hidden="true"></div>
    <div class="brand-name">VARNIK</div>
    <div class="brand-descriptor">Business Communications | Business Energy</div>
  </div>

  <div class="divider"></div>

  <div class="contact">
    <div class="contact__name">Daniel Reeves</div>
    <div class="contact__role">Owner</div>
    <ul class="contact__list">
      <li class="contact__item">
        <svg viewBox="0 0 24 24" aria-hidden="true"><path fill="#45ac0e" d="M6.6 10.8c1.4 2.8 3.8 5.1 6.6 6.6l2.2-2.2c.3-.3.7-.4 1-.2 1.1.4 2.3.6 3.6.6.6 0 1 .4 1 1V20c0 .6-.4 1-1 1C10.6 21 3 13.4 3 4c0-.6.4-1 1-1h3.5c.6 0 1 .4 1 1 0 1.3.2 2.5.6 3.6.1.3 0 .7-.2 1z"/></svg>
        044-987 654 321
      </li>
      <li class="contact__item">
        <svg viewBox="0 0 24 24" aria-hidden="true"><rect x="2" y="5" width="20" height="14" fill="#45ac0e"/><path d="M2 5l10 8 10-8" fill="none" stroke="#fff" stroke-width="2"/></svg>
        info@varnik-example.co.uk
      </li>
      <li class="contact__item">
        <svg viewBox="0 0 24 24" aria-hidden="true"><circle cx="12" cy="12" r="10" fill="#45ac0e"/><path d="M12 2v20M2 12h20M5 6c4 2 10 2 14 0M5 18c4-2 10-2 14 0" fill="none" stroke="#fff" stroke-width="1.4"/></svg>
        www.varnik-example.co.uk
      </li>
      <li class="contact__item">421, Address line goes here</li>
      <li class="contact__item">45452, Country name</li>
    </ul>
  </div>

  <div class="services">
    <div>• Business Mobile • Telephony • Internet</div>
    <div>• Business Energy Solutions</div>
  </div>

  <svg class="band" viewBox="0 0 724 12" preserveAspectRatio="none" aria-hidden="true">
    <polygon points="0,0 356,0 361,12 0,12" fill="#1c1466"/>
    <polygon points="361,0 724,0 724,12 366,12" fill="#45ac0e"/>
  </svg>
</section>

<section class="card card--back" aria-label="Card back">
  <div class="group-title">Varnik Holdings</div>
  <div class="back-brand">
    <div class="brand-mark" aria-hidden="true"></div>
    <div class="brand-name">VARNIK</div>
  </div>
</section>

</body>
</html>
```